Ridgeline Journeys business card

please see website
www.ridgelinejourneys.comau

info needed on card
Curtis Halvey
Ph
email
Adventure Riding GPS trails

please use my logo and colours off my site

Curtis Halvey
curtis@ridgelinejourneys.com

```html
<!DOCTYPE html>
<html lang="en">
<head>
<meta charset="utf-8">
<title>Ridgeline Journeys – Business Card</title>
<link rel="stylesheet" href="https://fonts.googleapis.com/css2?family=Source+Sans+3:ital,wght@0,400;0,600;1,600&display=swap">
<style>
  :root {
    --backdrop: #4a4a4a;
    --card: #f7f7f7;
    --ink: #111111;
    --ink-soft: #4a4a4a;
    --mark-grey: #555555;
    --accent-light: #f8ee3c;
    --accent-deep: #f4c300;
    --frame: #000000;
  }
  html, body {
    margin: 0;
    width: 1200px;
    height: 750px;
    overflow: hidden;
    background: var(--backdrop);
    font-family: "Source Sans 3", sans-serif;
  }
  .card {
    position: absolute;
    left: 100px;
    top: 90px;
    width: 1000px;
    height: 570px;
    background: var(--card);
    overflow: hidden;
  }
  .brand {
    position: absolute;
    left: 62px;
    top: 100px;
    display: flex;
    align-items: center;
    gap: 22px;
  }
  .brand-dot {
    width: 64px;
    height: 64px;
    border-radius: 50%;
    background: var(--mark-grey);
  }
  .brand-name {
    font-size: 46px;
    font-weight: 600;
    color: var(--ink);
    letter-spacing: 0.5px;
  }
  .contact {
    position: absolute;
    left: 59px;
    top: 344px;
  }
  .contact-name {
    margin: 0 0 18px;
    font-size: 35px;
    font-weight: 600;
    color: var(--ink);
  }
  .contact-line {
    margin: 0;
    font-size: 24px;
    line-height: 40px;
    color: var(--ink-soft);
  }
  .accent-panel {
    position: absolute;
    left: 560px;
    top: 0;
    width: 440px;
    height: 570px;
  }
  .tagline {
    position: absolute;
    right: 75px;
    bottom: 42px;
    margin: 0;
    font-size: 26px;
    font-style: italic;
    font-weight: 600;
    color: var(--ink);
  }
</style>
</head>
<body>
  <main class="card">
    <div class="brand">
      <span class="brand-dot"></span>
      <span class="brand-name">Ridgeline Journeys</span>
    </div>

    <section class="contact">
      <h1 class="contact-name">Curtis Halvey</h1>
      <p class="contact-line">Ph : 612 555 0147</p>
      <p class="contact-line">curtis@ridgelinejourneys.com</p>
      <p class="contact-line">www.ridgelinejourneys.comau</p>
    </section>

    <svg class="accent-panel" viewBox="0 0 440 570" role="img" aria-label="Large yellow brand decoration">
      <defs>
        <linearGradient id="accent-fill" x1="0" y1="0" x2="1" y2="1">
          <stop offset="0" stop-color="var(--accent-light)"/>
          <stop offset="1" stop-color="var(--accent-deep)"/>
        </linearGradient>
      </defs>
      <rect x="0" y="0" width="440" height="570" fill="var(--frame)"/>
      <rect x="16" y="16" width="408" height="538" fill="url(#accent-fill)"/>
    </svg>

    <p class="tagline">Adventure Riding GPS trails</p>
  </main>
</body>
</html>
```